Valdane Companies Business Card Design

We need a new business card for our Private Equity Real Estate Development firm, “Valdane” and our EB-5 regional center “Thornmere Regional Center” on one card. We prefer a design that is simple, elegant, and represents the luxury products we design and build as well as the financial security and stability our successful history has produced. We are an industry leader in our field and 3rd generation family business that has evolved into an institutional quality investment platform. Considered design size is standard business card dimensions (3.5 x 2 inches with an additional 1/8 inch space for design elements or backgrounds that extend beyond the finished size of your piece.

Target Market(s)

• High net worth individuals
• Highly skilled technical workers and physicians in the US seeking investment-based immigration opportunities
• Sophisticated private equity investors
• Intermediary partners include domestic attorneys and investment brokers, as well as international agent networks
• US real estate developers

Industry/Entity Type

Finance

Contact Information for Business Card

(Providing placeholder info for personal information, please design for longer character spaces, longer names and addresses etc..)
• Logo for Valdane
• Logo for Thornmere Regional Center
• Full name: Marcus Valdane
• Job title: CEO
• Email address: mvaldane@valdanecompanies.com
• Cell phone number: +1.555.314.2287
• Office number +1.555.628.4410
• Office address: Larkfield Court 5, 4817 Vista Orilla, Corvale Bay, CA.
• Website: www.valdanecompanies.com

Font styles to use
Serif
Sans Serif

Colors
ec1f27
ffffff
000000

Requirements
Must have
• • Logo for Valdane
• • Logo for Thornmere Regional Center
• - Use rounded corners
• (See .ai file included for logos)
Nice to have
• • Simple, elegant design
• • Aesthetically compatible with our website design (www.valdanecompanies.com)
• • Color palette including but not limited to white, black, and red (as per logos)
Should not have
• - Not too much red color
• - Do not stack both logos on top of each other

```html
<!DOCTYPE html>
<html lang="en">
<head>
<meta charset="utf-8">
<title>Valdane Companies Business Card</title>
<link rel="stylesheet" href="https://fonts.googleapis.com/css2?family=Open+Sans:wght@400;600&family=Tinos:wght@400;700&display=swap">
<style>
  :root {
    --stage: #2a2a2a;
    --card: #141414;
    --card-edge: #0a0a0a;
    --red: #ec1f27;
    --white: #ffffff;
    --silver: #9a9a9a;
    --muted: #7c7c7c;
  }
  * { margin: 0; padding: 0; box-sizing: border-box; }
  html, body { width: 1200px; height: 716px; overflow: hidden; }
  body {
    background: var(--stage);
    display: flex;
    align-items: center;
    justify-content: center;
    gap: 50px;
    font-family: "Open Sans", sans-serif;
  }
  .card {
    width: 525px;
    height: 300px;
    background: var(--card);
    border-radius: 22px;
    position: relative;
    overflow: hidden;
    box-shadow: 0 12px 30px rgba(0,0,0,.45);
    border: 1px solid var(--card-edge);
  }
  .front-brand {
    position: absolute;
    left: 0; right: 0; top: 96px;
    text-align: center;
    font-family: "Tinos", serif;
    font-weight: 700;
    color: var(--silver);
    font-size: 42px;
    letter-spacing: 3px;
    text-transform: uppercase;
  }
  .front-web {
    position: absolute;
    left: 0; right: 0; top: 200px;
    text-align: center;
    color: var(--muted);
    font-size: 15px;
    letter-spacing: 2.5px;
  }
  .center-brand {
    position: absolute;
    left: 36px; top: 32px;
    font-family: "Tinos", serif;
    font-weight: 700;
    color: var(--red);
    font-size: 20px;
    letter-spacing: 1.5px;
    text-transform: uppercase;
    line-height: 1.15;
    width: 200px;
  }
  .person {
    position: absolute;
    left: 200px; top: 108px;
    width: 300px;
  }
  .person-name {
    font-family: "Tinos", serif;
    color: var(--white);
    font-size: 24px;
    line-height: 1.15;
    letter-spacing: 1px;
    text-transform: uppercase;
  }
  .person-title {
    font-family: "Tinos", serif;
    color: var(--red);
    font-size: 14px;
    margin-top: 2px;
  }
  .contact-list {
    list-style: none;
    margin-top: 12px;
  }
  .contact-list li {
    display: flex;
    align-items: flex-start;
    gap: 9px;
    color: var(--white);
    font-size: 12.5px;
    line-height: 1.35;
    margin-bottom: 5px;
  }
  .contact-list svg { width: 13px; height: 13px; flex: none; margin-top: 2px; fill: var(--red); }
  .contact-list .address { margin-top: 6px; }
</style>
</head>
<body>
  <section class="card card-front">
    <div class="front-brand">Valdane Capital</div>
    <div class="front-web">www.valdanecompanies.com</div>
  </section>

  <section class="card card-back">
    <div class="center-brand">Thornmere Regional Center</div>
    <div class="person">
      <div class="person-name">Marcus Valdane</div>
      <div class="person-title">CEO</div>
      <ul class="contact-list">
        <li>
          <svg viewBox="0 0 16 16" aria-hidden="true"><rect x="1" y="3" width="14" height="10" rx="1"/></svg>
          mvaldane@valdanecompanies.com
        </li>
        <li>
          <svg viewBox="0 0 16 16" aria-hidden="true"><path d="M4 1h8a1 1 0 0 1 1 1v12a1 1 0 0 1-1 1H4a1 1 0 0 1-1-1V2a1 1 0 0 1 1-1zm1 2v9h6V3z"/></svg>
          +1.555.314.2287
        </li>
        <li>
          <svg viewBox="0 0 16 16" aria-hidden="true"><path d="M2 5c0-2 12-2 12 0v2h-3V5.5C9.5 5 6.5 5 5 5.5V7H2zm2 3h8l2 6H2z"/></svg>
          +1.555.628.4410
        </li>
        <li class="address">
          <svg viewBox="0 0 16 16" aria-hidden="true"><path d="M8 1a5 5 0 0 1 5 5c0 4-5 9-5 9S3 10 3 6a5 5 0 0 1 5-5zm0 3a2 2 0 1 0 0 4 2 2 0 0 0 0-4z"/></svg>
          <span>Larkfield Court 5, 4817 Vista Orilla<br>Corvale Bay, CA.</span>
        </li>
      </ul>
    </div>
  </section>
</body>
</html>
```